New Business Cards for Tormin Group

We need a new Business Card to compliment our new logo. We are a vibrant design, manufacture and install business providing recreation areas, public parks and Municipal spaces. We want business cards that are classy, modern and clean.

We have recently changed our logo, and are celebrating our 40th anniversary. We want business cards with a new modern design to reflect our status.

Target Market(s)

Customers

Contact Information for Business Card

We need all the details of our 3 offices as per the business card attached. Please disregard the old logo on the business card, the other three files show our new logo.

Requirements
Must have
• All info as per attached business card but with new logo.
Nice to have

```html
<!DOCTYPE html>
<html lang="en">
<head>
<meta charset="utf-8">
<title>Tormin Group — Business Card</title>
<link href="https://fonts.googleapis.com/css2?family=Open+Sans:wght@400;600;700&display=swap" rel="stylesheet">
<style>
  :root {
    --brand-red: #e8323a;
    --ink: #2b2b2b;
    --paper: #ffffff;
    --backdrop: #e4e4e4;
  }
  * { box-sizing: border-box; margin: 0; padding: 0; }
  html, body { width: 1200px; height: 1200px; overflow: hidden; }
  body {
    background: var(--backdrop);
    font-family: "Open Sans", Arial, sans-serif;
    color: var(--ink);
    position: relative;
  }
  .card {
    position: absolute;
    left: 250px;
    width: 700px;
    height: 400px;
    overflow: hidden;
    box-shadow: 0 8px 24px rgba(0,0,0,0.18);
  }
  /* Front */
  .card-front {
    top: 160px;
    background: var(--brand-red);
    border-radius: 90px 0 90px 0;
    display: flex;
    align-items: center;
    justify-content: center;
  }
  .wordmark {
    display: flex;
    align-items: center;
    gap: 22px;
    font-weight: 700;
    letter-spacing: 1px;
    text-transform: uppercase;
  }
  .wordmark-dot { border-radius: 50%; flex: none; }
  .card-front .wordmark { color: var(--paper); font-size: 52px; }
  .card-front .wordmark-dot { width: 110px; height: 110px; background: var(--paper); }

  /* Back */
  .card-back {
    top: 640px;
    background: var(--paper);
    border-radius: 0 90px 0 90px;
  }
  .holder { position: absolute; left: 40px; top: 34px; }
  .holder-name {
    color: var(--brand-red);
    font-size: 19px;
    font-weight: 700;
    text-transform: uppercase;
    line-height: 1.2;
  }
  .holder-title { font-size: 12px; margin-bottom: 6px; }
  .contact-line { font-size: 12.5px; line-height: 1.5; }
  .label { color: var(--brand-red); font-weight: 700; margin-right: 4px; }

  .card-back .wordmark {
    position: absolute;
    right: 44px;
    top: 60px;
    color: var(--brand-red);
    font-size: 32px;
    gap: 14px;
  }
  .card-back .wordmark-dot { width: 76px; height: 76px; background: var(--brand-red); }

  .offices {
    position: absolute;
    left: 40px;
    right: 30px;
    top: 172px;
    display: grid;
    grid-template-columns: repeat(3, 1fr);
    column-gap: 18px;
  }
  .office-name {
    color: var(--brand-red);
    font-size: 16px;
    font-weight: 700;
    margin-bottom: 4px;
  }
  .office .contact-line { font-size: 12.5px; line-height: 1.55; }

  .web-band {
    position: absolute;
    left: 0; right: 0; bottom: 0;
    height: 62px;
    background: var(--brand-red);
    color: var(--paper);
    font-size: 16px;
    display: flex;
    align-items: center;
    justify-content: center;
    letter-spacing: 0.5px;
  }
</style>
</head>
<body>

  <section class="card card-front">
    <div class="wordmark">
      <span class="wordmark-dot"></span>
      <span class="wordmark-name">Tormin Group</span>
    </div>
  </section>

  <section class="card card-back">
    <div class="holder">
      <p class="holder-name">Rami Haddad</p>
      <p class="holder-title">Managing Partner</p>
      <p class="contact-line"><span class="label">M:</span>+971 (0)50 318 4720</p>
      <p class="contact-line"><span class="label">E:</span>rami@tormingroup.com</p>
    </div>

    <div class="wordmark">
      <span class="wordmark-dot"></span>
      <span class="wordmark-name">Tormin Group</span>
    </div>

    <div class="offices">
      <div class="office">
        <p class="office-name">Head Office</p>
        <p class="contact-line">P.O.Box:10482 Abu Dhabi,<br>U.A.E.</p>
        <p class="contact-line"><span class="label">P :</span>+971 (0)2 5170392</p>
        <p class="contact-line"><span class="label">F :</span>+971 (0)2 5170393</p>
        <p class="contact-line"><span class="label">E :</span>sales@tormingroup.com</p>
      </div>
      <div class="office">
        <p class="office-name">Dubai Office</p>
        <p class="contact-line">P.O.Box:275140 Dubai,<br>U.A.E.</p>
        <p class="contact-line"><span class="label">P :</span>+971 (0)4 3862047</p>
        <p class="contact-line"><span class="label">F :</span>+971 (0)2 3862058</p>
        <p class="contact-line"><span class="label">E :</span>sales@tormingroup.com</p>
      </div>
      <div class="office">
        <p class="office-name">Qatar Office</p>
        <p class="contact-line">P.O.Box:20931 Doha,<br>Qatar</p>
        <p class="contact-line"><span class="label">P :</span>+974 44715830</p>
        <p class="contact-line"><span class="label">F :</span>+971 44602917</p>
        <p class="contact-line"><span class="label">E :</span>sales@tormingroup.com</p>
      </div>
    </div>

    <div class="web-band">www.tormingroup.com</div>
  </section>

</body>
</html>
```